Harbourline Physiotherapy business card design

We need a fresh, new business card design for our physiotherapy clinic Harbourline Physiotherapy

Will attach logo soon we had logo designed from our last project

Industry/Entity Type

Physical Therapy

Contact Information for Business Card

On front
Needs our logo, contact details:
58 Wexley Lane Tallowbrook NSW 2990
Ph/f: 02 9481 2057
info@harbourlinephysio.example.com.au

Requirements
Must have
• On the back of the card needs to have area to write down follow up appointments
• On front
• Needs our logo
• The colours have to be the colours in our logo which are: sky blue, black and white
• Font to be same as our logo please
• We want the card to look simple, not too cluttered but to the point
Should not have
• We don't need any extra pictures other than our logo

```html
<!DOCTYPE html>
<html lang="en">
<head>
<meta charset="utf-8">
<title>Harbourline Physiotherapy – Business Card</title>
<link rel="stylesheet" href="https://fonts.googleapis.com/css2?family=Open+Sans:ital,wght@0,400;0,600;0,700;0,800;1,400&display=swap">
<style>
  :root {
    --page-bg: #e6e4e1;
    --card-bg: #f8f8f8;
    --card-edge: #dcdcdc;
    --band-dark: #4b4b50;
    --ink: #3c3c40;
    --ink-soft: #6a6a70;
    --sky-blue: #2e8fd8;
    --white: #ffffff;
  }
  * { box-sizing: border-box; margin: 0; padding: 0; }
  html, body {
    width: 1200px; height: 692px; overflow: hidden;
    background: var(--page-bg);
    font-family: "Open Sans", Arial, sans-serif;
    color: var(--ink);
  }
  .canvas { position: relative; width: 1200px; height: 692px; }

  .card {
    position: absolute; top: 191px;
    width: 540px; height: 310px;
    background: linear-gradient(160deg, var(--white) 0%, var(--card-bg) 100%);
    border: 1px solid var(--card-edge);
    border-radius: 6px;
    box-shadow: 0 6px 18px rgba(0,0,0,.12);
    overflow: hidden;
  }
  .card--front { left: 40px; }
  .card--back { left: 620px; }

  .band {
    position: absolute;
    background: var(--band-dark);
    color: var(--white);
    display: flex; align-items: center;
  }
  .band--top {
    top: 26px; left: 0; height: 40px;
    border-radius: 0 20px 20px 0;
    padding: 0 26px 0 30px;
  }
  .band--bottom {
    right: 0; bottom: 24px;
    border-radius: 30px 0 0 30px;
  }

  /* Front */
  .tagline { width: 330px; font-size: 14px; font-weight: 400; }
  .brand {
    position: absolute; left: 34px; top: 128px;
    display: flex; align-items: center; gap: 10px;
  }
  .brand__dot { width: 22px; height: 22px; border-radius: 50%; background: var(--sky-blue); flex: none; }
  .brand__name {
    font-size: 22px; font-weight: 600; line-height: 1.1; color: var(--sky-blue);
  }
  .contact {
    position: absolute; left: 292px; top: 112px;
    font-size: 12px; line-height: 1.7; color: var(--ink-soft);
    font-style: normal;
  }
  .contact__label { color: var(--sky-blue); font-weight: 600; }
  .contact__phone { color: var(--ink); font-weight: 600; }
  .services {
    width: 350px; height: 56px; padding-left: 28px;
    flex-direction: column; align-items: flex-start; justify-content: center;
    font-size: 11px; line-height: 1.7; white-space: nowrap;
  }
  .services__sep { color: var(--sky-blue); margin: 0 4px; }

  /* Back */
  .appointment-title {
    width: 262px; font-size: 15px; font-weight: 800; letter-spacing: .8px;
  }
  .form-row {
    position: absolute; left: 30px;
    display: flex; align-items: center;
    font-size: 12px; font-weight: 700; color: var(--ink);
  }
  .form-row--date { top: 94px; }
  .form-row--days { top: 136px; gap: 12px; }
  .form-row--therapist { top: 184px; }
  .fill-line {
    display: inline-block; height: 1px; margin: 6px 8px 0 6px;
    border-bottom: 1.5px dashed var(--ink);
  }
  .fill-line--date { width: 130px; }
  .fill-line--time { width: 80px; }
  .fill-line--therapist { width: 300px; }
  .option { display: inline-flex; align-items: center; gap: 4px; margin-left: 8px; }
  .form-row--days .option { margin-left: 0; }
  .tick-box {
    display: inline-block; width: 14px; height: 14px;
    border: 1.6px solid var(--sky-blue); border-radius: 3px; background: var(--white);
  }
  .timings {
    width: 336px; height: 80px; padding: 0 20px 0 30px;
    flex-direction: column; align-items: flex-start; justify-content: center;
    font-size: 11.5px; line-height: 1.55;
  }
  .timings__title { color: var(--sky-blue); font-weight: 700; font-size: 12px; }
  .timings__grid {
    display: grid; grid-template-columns: 150px 140px; column-gap: 8px;
  }
  .timings__day { font-weight: 700; }
</style>
</head>
<body>
<main class="canvas">

  <section class="card card--front" aria-label="Card front">
    <div class="band band--top">
      <p class="tagline">Best possible outcome for all patients.</p>
    </div>

    <div class="brand">
      <span class="brand__dot"></span>
      <p class="brand__name">Harbourline<br>Physiotherapy</p>
    </div>

    <address class="contact">
      <p><span class="contact__label">Phone:</span> <span class="contact__phone">02 9481 2057</span></p>
      <p>info@harbourlinephysio.example.com.au</p>
      <p>58 Wexley Lane, Tallowbrook NSW 2990</p>
    </address>

    <div class="band band--bottom services">
      <p>Hydrotherapy<span class="services__sep">•</span>Sports Injuries<span class="services__sep">•</span>Back &amp; Neck Pain</p>
      <p>Chronic Pain Management<span class="services__sep">•</span>Physiotherapy Treatment</p>
    </div>
  </section>

  <section class="card card--back" aria-label="Card back">
    <div class="band band--top">
      <h2 class="appointment-title">NEXT APPOINTMENT</h2>
    </div>

    <div class="form-row form-row--date">
      DATE:<span class="fill-line fill-line--date"></span>
      TIME:<span class="fill-line fill-line--time"></span>
      <span class="option">AM <span class="tick-box"></span></span>
      <span class="option">PM <span class="tick-box"></span></span>
    </div>

    <div class="form-row form-row--days">
      <span class="option">Mon <span class="tick-box"></span></span>
      <span class="option">Tue <span class="tick-box"></span></span>
      <span class="option">Wed <span class="tick-box"></span></span>
      <span class="option">Thu <span class="tick-box"></span></span>
      <span class="option">Fri <span class="tick-box"></span></span>
      <span class="option">Sat <span class="tick-box"></span></span>
      <span class="option">Sun <span class="tick-box"></span></span>
    </div>

    <div class="form-row form-row--therapist">
      NAME OF THERAPIST:<span class="fill-line fill-line--therapist"></span>
    </div>

    <div class="band band--bottom timings">
      <p class="timings__title">Our Timings:</p>
      <div class="timings__grid">
        <p><span class="timings__day">Mon:</span> 8am - 5:30pm</p>
        <p><span class="timings__day">Wed:</span> 10am - 4pm</p>
        <p><span class="timings__day">Tues:</span> 10:30am - 8pm</p>
        <p><span class="timings__day">Thur:</span> 10am - 6pm</p>
        <p></p>
        <p><span class="timings__day">Fri:</span> 8am - 5:30pm</p>
      </div>
    </div>
  </section>

</main>
</body>
</html>
```